TalbeckLabs needs a new rocket based website

We need a new website that will be based on our rocket ship logo. We develop innovative solutions for enterprises. We would like to see a design that when the pages scroll, the rocket launches and goes from launch through a journey, similar to how we approach our customer. We would like areas for "Who are we", "What can we do", "What have we done", "How can we help". http://www.talbecklabs.example.au is our current website

Target Market(s)

Government, Enterprise, Cloud

Industry/Entity Type

Software Service

Coding

Coded - Design and coding required

Number of Pages Required

2 page

Requirements
Must have
• We would like to see a design that when the pages scroll, the rocket launches and goes from launch through a journey, similar to how we approach our customer.
• Must have a home page and a detail page.
• Would like to see the logo/rocket animate in some way when you scroll through he page.

```html
<!DOCTYPE html>
<html lang="en">
<head>
<meta charset="utf-8">
<title>TalbeckLabs – Innovative Software Solutions</title>
<link rel="stylesheet" href="https://fonts.googleapis.com/css2?family=Poppins:wght@400;500;600&display=swap">
<style>
:root{
  --orange:#f7941d;
  --orange-dark:#e8860f;
  --ink:#2b2b2b;
  --muted:#666;
  --navy:#0d1a2e;
  --night:#111418;
  --tile:#efefef;
  --white:#fff;
  --line:#d9d9d9;
  --footer:#141414;
}
*{margin:0;padding:0;box-sizing:border-box}
html,body{width:1200px;height:3383px;overflow:hidden}
body{position:relative;font-family:'Poppins',sans-serif;color:var(--ink);background:var(--white)}
.abs{position:absolute}
.brand{display:flex;align-items:center;gap:10px;font-weight:600;color:var(--white)}
.brand-dot{width:18px;height:18px;border-radius:50%;background:var(--orange)}

/* hero */
.hero{left:0;top:0;width:1200px;height:710px;
  background:linear-gradient(180deg,#0b1526 0%,#17263e 45%,#3b4a60 62%,#dfe4ea 78%,#ffffff 100%)}
.hero-nav{left:117px;top:20px;width:966px;height:32px;display:flex;align-items:center;justify-content:space-between}
.hero-nav .brand{font-size:26px}
.nav-links{display:flex;gap:34px;font-size:15px;font-weight:500;color:var(--white);align-items:center}
.hero-mark{left:0;top:160px;width:1200px;display:flex;justify-content:center;align-items:center;gap:30px}
.hero-mark .rule{width:150px;height:2px;background:var(--orange)}
.hero-mark .brand{font-size:32px}
.hero-title{left:0;top:245px;width:1200px;text-align:center;color:var(--white);font-size:49px;font-weight:600;line-height:58px}
.hero-link{left:0;top:380px;width:1200px;text-align:center;color:var(--orange);font-size:16px;font-weight:500}
.hero-arrow{width:46px;height:46px;border-radius:50%;top:300px;display:flex;align-items:center;justify-content:center}
.hero-arrow.prev{left:29px;background:rgba(255,255,255,.35)}
.hero-arrow.next{left:1125px;background:rgba(0,0,0,.6)}

/* journey path */
.journey{left:0;top:0;width:1200px;height:3383px;pointer-events:none}
.waypoint{width:60px;height:60px;border-radius:50%;background:var(--white);box-shadow:0 2px 8px rgba(0,0,0,.2);display:flex;align-items:center;justify-content:center}
.waypoint span{width:14px;height:14px;border-radius:50%;background:var(--orange)}

/* sections */
.section-title{color:var(--orange);font-weight:600;font-size:34px}
.body-text{font-size:15px;line-height:27px}
.who-title{left:112px;top:805px}
.who-text{left:112px;top:858px;width:430px;color:var(--muted)}
.who-sub{left:112px;top:962px;color:var(--orange);font-size:19px;font-weight:500}
.who-contact{left:112px;top:1000px;font-size:15px;line-height:29px;color:var(--muted)}
.tile{width:244px;height:142px;background:var(--tile);display:flex;flex-direction:column;align-items:center;justify-content:flex-end;padding-bottom:16px;gap:12px;font-size:16px;font-weight:500;color:var(--ink)}
.tile.active{background:var(--orange);color:var(--white)}

.done{left:0;top:1166px;width:1200px;height:515px;
  background:linear-gradient(90deg,#131417 0%,#1c2026 45%,#2a3a46 75%,#1f3442 100%)}
.done-title{left:133px;top:1247px}
.done-text{left:133px;top:1310px;width:560px;color:#e6e6e6;font-size:15px;line-height:27.5px}
.btn{display:flex;align-items:center;justify-content:center;background:var(--orange);color:var(--white);font-weight:500;border-radius:22px}
.done-btn{left:133px;top:1558px;width:145px;height:38px;font-size:15px}

.do-title{left:0;top:1742px;width:1200px;text-align:center}
.service{width:230px}
.service-photo{width:230px;height:158px}
.service h3{margin-top:33px;text-align:center;color:var(--orange);font-size:19px;font-weight:500}
.service p{margin-top:10px;text-align:center;color:var(--muted);font-size:13.5px;line-height:24px;padding:0 12px}

.help{left:0;top:2193px;width:1200px;height:472px;
  background:radial-gradient(ellipse at 75% 40%,#2c3138 0%,#16191d 55%,#0c0e10 100%)}
.help-title{left:0;top:2286px;width:1200px;text-align:center;color:var(--white);font-size:34px;font-weight:500}
.help-sub{left:0;top:2346px;width:1200px;text-align:center;color:var(--white);font-size:21px;line-height:31px}
.help-btn{left:510px;top:2439px;width:171px;height:42px;font-size:17px}

.customers{left:106px;top:2563px;width:979px;height:408px;background:var(--white);box-shadow:0 4px 18px rgba(0,0,0,.12)}
.cust-title{left:0;top:52px;width:979px;text-align:center}
.client{width:420px;text-align:center}
.client h3{color:var(--orange);font-size:21px;font-weight:500}
.client p{margin-top:16px;color:var(--muted);font-size:14px;line-height:24.5px}
.client .name{margin-top:12px;color:var(--ink);font-size:16px}
.client .name b{color:var(--orange);font-weight:500}

.footer{left:0;top:3039px;width:1200px;height:344px;background:var(--footer);color:var(--white)}
.footer .brand{font-size:28px}
.foot-about{font-size:14.5px;line-height:25px}
.foot-head{font-size:17px;font-weight:500}
.foot-list{list-style:none;font-size:14px;line-height:30px}
.foot-contact{font-size:14px;line-height:24px}
.foot-contact b{font-weight:600}
.social{width:30px;height:30px;border-radius:50%;background:var(--white)}
.copyright{left:0;top:3333px;width:1200px;text-align:center;font-size:14.5px}
</style>
</head>
<body>

<!-- hero -->
<section class="abs hero" role="img" aria-label="Rocket lifting off into a night sky above a bank of white cloud">
</section>
<header class="abs hero-nav">
  <div class="brand"><span class="brand-dot"></span>TalbeckLabs</div>
  <nav class="nav-links">
    <span>Home</span><span>About Us</span><span>Services</span><span>Contact Us</span>
    <svg width="16" height="16" viewBox="0 0 16 16"><circle cx="6.5" cy="6.5" r="5" fill="none" stroke="#fff" stroke-width="2"/><line x1="10.5" y1="10.5" x2="15" y2="15" stroke="#fff" stroke-width="2"/></svg>
  </nav>
</header>
<div class="abs hero-mark"><span class="rule"></span><div class="brand"><span class="brand-dot"></span>TalbeckLabs</div><span class="rule"></span></div>
<h1 class="abs hero-title">Innovative Software<br>Solutions</h1>
<div class="abs hero-link">Find Out More &rsaquo;</div>
<div class="abs hero-arrow prev"><svg width="12" height="14"><path d="M8 2 3 7l5 5" fill="none" stroke="#fff" stroke-width="2"/></svg></div>
<div class="abs hero-arrow next"><svg width="12" height="14"><path d="M4 2l5 5-5 5" fill="none" stroke="#fff" stroke-width="2"/></svg></div>

<!-- who we are -->
<h2 class="abs section-title who-title">Who We Are</h2>
<p class="abs body-text who-text">Lorem ipsum dolor sit amet, consectetur adipiscing elit, sed do eiusmod tempor incididunt ut labore et dolore magna aliqua.</p>
<div class="abs who-sub">For Multiple Queries :.</div>
<div class="abs who-contact">Phone : &nbsp;1300 000 417<br>Email : &nbsp;info@talbecklabs.example.au</div>

<div class="abs tile active" style="left:584px;top:819px">
  <svg width="74" height="70" viewBox="0 0 74 70" fill="none" stroke="#fff" stroke-width="2.5"><path d="M6 22 37 5l31 17z"/><line x1="8" y1="26" x2="66" y2="26"/><line x1="16" y1="30" x2="16" y2="56"/><line x1="29" y1="30" x2="29" y2="56"/><line x1="45" y1="30" x2="45" y2="56"/><line x1="58" y1="30" x2="58" y2="56"/><rect x="6" y="58" width="62" height="6"/></svg>
  e-Parliament
</div>
<div class="abs tile" style="left:841px;top:819px">
  <svg width="74" height="70" viewBox="0 0 74 70" fill="none" stroke="#222" stroke-width="2.5"><path d="M18 30a12 12 0 0 1 4-23 15 15 0 0 1 28 3 10 10 0 0 1 4 20z"/><rect x="20" y="36" width="34" height="9"/><rect x="20" y="47" width="34" height="9"/><rect x="20" y="58" width="34" height="9"/></svg>
  Cloud
</div>
<div class="abs tile" style="left:584px;top:975px">
  <svg width="74" height="70" viewBox="0 0 74 70" fill="none" stroke="#222" stroke-width="2.5"><rect x="6" y="14" width="52" height="50"/><path d="M14 56 52 18l6 6-38 38z"/><line x1="6" y1="30" x2="14" y2="30"/><line x1="6" y1="42" x2="14" y2="42"/></svg>
  Architecture &amp; Design
</div>
<div class="abs tile" style="left:841px;top:975px">
  <svg width="74" height="70" viewBox="0 0 74 70" fill="none" stroke="#222" stroke-width="2.5"><rect x="6" y="18" width="50" height="34"/><line x1="22" y1="62" x2="40" y2="62"/><line x1="31" y1="52" x2="31" y2="62"/><circle cx="54" cy="18" r="10"/><circle cx="54" cy="18" r="4"/></svg>
  Software Development
</div>

<!-- what have we done -->
<section class="abs done" role="img" aria-label="Portrait of a developer lit by screens of code and data overlays"></section>
<h2 class="abs section-title done-title">What Have We Done</h2>
<p class="abs done-text">Sed ut perspiciatis unde omnis iste natus error sit voluptatem accusantium doloremque laudantium, totam rem aperiam, eaque ipsa quae ab illo inventore veritatis et quasi architecto beatae vitae dicta sunt explicabo. Nemo enim ipsam voluptatem quia voluptas sit aspernatur aut odit aut fugit, sed quia consequuntur magni dolores eos qui ratione voluptatem sequi nesciunt. Neque porro quisquam est, qui dolorem ipsum quia dolor sit amet, consectetur, adipisci velit, sed quia non numquam eius modi tempora incidunt ut</p>
<div class="abs btn done-btn">Read More</div>

<!-- what can we do -->
<h2 class="abs section-title do-title">What Can We Do</h2>
<article class="abs service" style="left:110px;top:1820px">
  <div class="service-photo" role="img" aria-label="Parliament building with flags at dusk" style="background:linear-gradient(180deg,#6f93c4,#2d3f5c 70%,#1c2233)"></div>
  <h3>e-Parliament</h3>
  <p>All of your Parliamentary software &amp; business process needs.</p>
</article>
<article class="abs service" style="left:359px;top:1820px">
  <div class="service-photo" role="img" aria-label="Cloud computing concept in blue tones" style="background:linear-gradient(180deg,#b9d8ef,#4a8cc4 60%,#1f4f82)"></div>
  <h3>Cloud</h3>
  <p>Office Suite, Migration, Security, Customisations,</p>
</article>
<article class="abs service" style="left:607px;top:1820px">
  <div class="service-photo" role="img" aria-label="Modern glass skyscrapers seen from below" style="background:linear-gradient(135deg,#f1b04a,#6a4b3a 50%,#24324a)"></div>
  <h3>Architecture &amp; Design</h3>
  <p>Business process design, technology strategy and architecture.</p>
</article>
<article class="abs service" style="left:855px;top:1820px">
  <div class="service-photo" role="img" aria-label="Screen of programming code" style="background:linear-gradient(135deg,#0e2a3d,#1b6f8f 55%,#e08a3c)"></div>
  <h3>Software Development</h3>
  <p>Software development including business apps, web and mobile..</p>
</article>

<!-- how can we help -->
<section class="abs help" role="img" aria-label="Hands typing on a laptop beneath a network of connected nodes"></section>
<h2 class="abs help-title">How Can We Help</h2>
<p class="abs help-sub">We are an established business that has been<br>around for over 15 years</p>
<div class="abs btn help-btn">Contact Us</div>

<!-- customers -->
<section class="abs customers">
  <h2 class="abs section-title cust-title">Our Customers</h2>
  <div class="abs client" style="left:40px;top:152px">
    <h3>Parliament of Eastmere</h3>
    <p>Donec sed eros fermentum, cursus dui eget, bibendum nibh. Donec scelerisque sollicitudin magna, in viverra lacus placerat quis. Maecenas tincidunt nisl</p>
    <div class="name">Client: <b>Mara Quill</b></div>
  </div>
  <div class="abs client" style="left:505px;top:152px">
    <h3>Parliament of Northvale</h3>
    <p>Donec sed eros fermentum, cursus dui eget, bibendum nibh. Donec scelerisque sollicitudin magna, in viverra lacus placerat quis. Maecenas tincidunt nisl</p>
    <div class="name">Client: <b>Ted Orwin</b></div>
  </div>
</section>

<!-- journey path -->
<svg class="abs journey" viewBox="0 0 1200 3383" fill="none" stroke="#cfcfcf" stroke-width="1.5">
  <path d="M541 750 V1083 H106 V1166"/>
  <path d="M106 1166 V1718 H1122 V2250 H980" stroke="#bdbdbd"/>
  <g fill="#f7941d" stroke="none">
    <circle cx="541" cy="910" r="5"/><circle cx="320" cy="1083" r="5"/>
    <circle cx="106" cy="1510" r="5"/><circle cx="320" cy="1718" r="5"/>
    <circle cx="1066" cy="1718" r="5"/><circle cx="1122" cy="2055" r="5"/>
    <circle cx="1010" cy="2250" r="5"/>
  </g>
</svg>
<div class="abs waypoint" style="left:511px;top:692px"><span></span></div>
<div class="abs waypoint" style="left:76px;top:1178px"><span></span></div>
<div class="abs waypoint" style="left:561px;top:1688px;width:44px;height:44px"><span></span></div>
<div class="abs waypoint" style="left:561px;top:2222px"><span></span></div>

<!-- footer -->
<footer class="abs footer">
  <div class="abs brand" style="left:114px;top:50px"><span class="brand-dot"></span>TalbeckLabs</div>
  <p class="abs foot-about" style="left:114px;top:108px;width:260px">Lorem ipsum dolor sit amet, consectetur adipiscing elit, sed do eiusmod tempor incididunt ut labore et dolore magna aliqua.</p>
  <div class="abs social" style="left:170px;top:234px"></div>

  <h4 class="abs foot-head" style="left:429px;top:48px">Quick Links</h4>
  <ul class="abs foot-list" style="left:429px;top:100px"><li>Home</li><li>About Us</li><li>Services</li><li>Contact Us</li></ul>

  <h4 class="abs foot-head" style="left:620px;top:48px">Services</h4>
  <ul class="abs foot-list" style="left:620px;top:100px"><li>e-Parliament</li><li>Cloud</li><li>Architecture &amp; Design</li><li>Software Development</li></ul>

  <h4 class="abs foot-head" style="left:855px;top:48px">Contact Us</h4>
  <div class="abs foot-contact" style="left:858px;top:103px;width:260px">
    <b>Address:</b> &nbsp;Unit 7, 41 Ferncliff Rd<br>Brayton, SA 5999
    <div style="margin-top:14px"><b>Phone:</b> &nbsp;1300 000 417</div>
    <div style="margin-top:14px"><b>Email:</b> &nbsp;info@talbecklabs.example.au</div>
  </div>
  <div class="abs copyright" style="top:294px">© 2018 Copyrights | All Rights Reserved</div>
</footer>

</body>
</html>
```